RB Halden Electric Yard Sign

Looking to have a yard sign designed that we can place at projects we are working on. Most likely will be 18" H x 24" W but flexible that we can increase the size if necessary. It should include our logo, our phone # 609-555-0147, website rbhaldenelectric.example and slogan, built on integrity, driven by excellence. Colors should match our brand.

```html
<!DOCTYPE html>
<html lang="en">
<head>
<meta charset="utf-8">
<title>RB Halden Electric Yard Sign</title>
<link rel="stylesheet" href="https://fonts.googleapis.com/css2?family=Archivo:wdth,wght@125,800&family=Josefin+Sans:wght@600&family=Saira+Extra+Condensed:ital,wght@1,700&display=swap">
<style>
  :root {
    --backdrop: #505050;
    --sign-white: #ffffff;
    --brand-red: #e21f2d;
    --brand-navy: #06365a;
  }
  html, body {
    margin: 0;
    width: 1200px;
    height: 1001px;
    overflow: hidden;
    background: var(--backdrop);
  }
  .yard-sign {
    position: absolute;
    left: 124px;
    top: 142px;
    width: 952px;
    height: 714px;
    display: block;
  }
  .company-name { font-family: "Archivo", sans-serif; font-stretch: 125%; font-weight: 800; fill: var(--brand-red); }
  .company-role { font-family: "Josefin Sans", sans-serif; font-weight: 600; fill: var(--brand-navy); }
  .contact-phone, .contact-web { font-family: "Archivo", sans-serif; font-stretch: 125%; font-weight: 800; fill: var(--sign-white); }
  .slogan { font-family: "Saira Extra Condensed", sans-serif; font-style: italic; font-weight: 700; fill: var(--brand-navy); }
  .red { fill: var(--brand-red); }
  .navy { fill: var(--brand-navy); }
</style>
</head>
<body>
<svg class="yard-sign" viewBox="0 0 952 714" xmlns="http://www.w3.org/2000/svg">
  <rect class="sign-panel" width="952" height="714" fill="var(--sign-white)"/>

  <!-- brand name -->
  <text class="company-name" x="476" y="240" font-size="64" text-anchor="middle" textLength="620" lengthAdjust="spacingAndGlyphs">RB HALDEN</text>
  <text class="company-role" x="473" y="290" font-size="42" text-anchor="middle" textLength="618" lengthAdjust="spacing">Electrical Contractor</text>

  <!-- header underline -->
  <path class="red" d="M156 296 L778 296 L764 301 L170 301 Z"/>
  <rect class="navy" x="170" y="301" width="594" height="5"/>

  <!-- contact band -->
  <rect class="red" x="0" y="341" width="952" height="10"/>
  <rect class="navy" x="0" y="351" width="952" height="209"/>
  <rect class="red" x="0" y="560" width="952" height="10"/>

  <g class="icon-phone red" transform="translate(76 400)">
    <path d="M6 2 C2 6 0 14 4 26 C9 38 18 46 28 50 C32 51 36 49 38 46 L33 38 C31 36 28 36 26 38 L23 40 C18 37 13 30 11 24 L14 21 C16 19 16 16 14 14 L10 2 Z"/>
  </g>
  <text class="contact-phone" x="117" y="450" font-size="66" textLength="760" lengthAdjust="spacingAndGlyphs">609-555-0147</text>

  <g class="icon-globe" transform="translate(98 505)" fill="none" stroke="var(--brand-red)" stroke-width="3">
    <circle r="17"/>
    <ellipse rx="7" ry="17"/>
    <line x1="-17" y1="0" x2="17" y2="0"/>
    <line x1="-14" y1="-8" x2="14" y2="-8"/>
    <line x1="-14" y1="8" x2="14" y2="8"/>
    <line x1="0" y1="-17" x2="0" y2="17"/>
  </g>
  <text class="contact-web" x="134" y="521" font-size="44" textLength="740" lengthAdjust="spacingAndGlyphs">rbhaldenelectric.example</text>

  <!-- slogan -->
  <text class="slogan" x="477" y="653" font-size="64" text-anchor="middle" textLength="786" lengthAdjust="spacingAndGlyphs">BUILT ON INTEGRITY, DRIVEN BY EXCELLENCE</text>

  <!-- footer underline -->
  <path class="red" d="M14 672 L938 672 L918 679 L34 679 Z"/>
  <rect class="navy" x="34" y="679" width="884" height="6"/>
</svg>
</body>
</html>
```